Fresh, modern, fun business card for pediatric dental practice

Need a business card for fresh, modern, fun pediatric dental practice

Clean look that matches our website's font and colors

We prefer the look of curved corners on business cards

Target Market(s)

parents (mothers) of young children, professionals, mid-high class

Industry/Entity Type

Dental

Contact Information for Business Card

Maplebrook Pediatric Dentistry
482 Quarry Lane
Suite 517
Fernvale, PA 17588
717.555.0193
www.maplebrookkidsdental.example

Mei-Ran Tsai, DMD
Corinne Walbeck, DMD
(we are working on our email address, but we would like that on the card as well)

Font styles to use
Sans Serif

Requirements
Must have
• All info; we would also like to make cards for individual staff members
• colors from our website and color palatte, attatched
• use same font and design as website for branding
Nice to have
• clean, simple card that has a pop of color
• we would like to see a few designs with our tag line "where smiles get brighter"
• we are not sure if we want to have it on there or not
• we would like to see a few designs incorporating the ribbon graphic on our website where the word WELCOME is

```html
<!DOCTYPE html>
<html lang="en">
<head>
<meta charset="utf-8">
<title>Maplebrook Pediatric Dentistry – Business Card</title>
<link href="https://fonts.googleapis.com/css2?family=Open+Sans:wght@600&family=Roboto:wght@400&family=Roboto+Condensed:wght@500&display=swap" rel="stylesheet">
<style>
  :root {
    --backdrop: #2b2b2b;
    --card-white: #f3f3f3;
    --sun-yellow: #f0b323;
    --text-grey: #454545;
    --white: #ffffff;
  }
  * { margin: 0; padding: 0; box-sizing: border-box; }
  html, body { width: 1200px; height: 960px; overflow: hidden; }
  body { background: var(--backdrop); position: relative; font-family: "Roboto", sans-serif; }

  .card {
    position: absolute;
    width: 600px;
    height: 343px;
    border-radius: 22px;
  }
  .card-front { left: 314px; top: 113px; background: var(--card-white); }
  .card-back  { left: 311px; top: 472px; background: var(--sun-yellow); }

  /* front */
  .brand-front {
    position: absolute; right: 40px; top: 46px;
    text-align: right; color: var(--sun-yellow);
    font-family: "Open Sans", sans-serif; font-weight: 600;
  }
  .brand-mark {
    display: block; width: 26px; height: 26px; border-radius: 50%;
    background: var(--sun-yellow); margin: 0 76px 12px auto;
  }
  .brand-name { font-size: 40px; line-height: 44px; letter-spacing: 0.5px; }
  .brand-sub  { font-size: 19px; line-height: 24px; letter-spacing: 0.6px; }

  .doctors {
    position: absolute; left: 45px; top: 164px;
    font-family: "Roboto Condensed", sans-serif; font-weight: 500;
    font-size: 21px; line-height: 24px; color: var(--sun-yellow);
  }
  .doctors li { list-style: none; }
  .doctors li:nth-child(2) { margin-left: -1px; }

  .contact {
    position: absolute; right: 40px; top: 247px;
    text-align: right; font-size: 14.5px; line-height: 18px; color: var(--text-grey);
  }
  .contact-line { display: flex; justify-content: flex-end; align-items: center; gap: 3px; }
  .contact-line svg { width: 13px; height: 13px; }
  .contact-line .gap { width: 4px; }

  /* back */
  .brand-back {
    position: absolute; left: 0; right: 0; top: 118px;
    text-align: center; color: var(--white);
    font-family: "Open Sans", sans-serif; font-weight: 600;
  }
  .brand-back .brand-mark { background: var(--white); width: 30px; height: 30px; margin: 0 auto 14px; }
  .brand-back .brand-name { font-size: 44px; line-height: 48px; }
  .brand-back .brand-sub  { font-size: 21px; line-height: 26px; letter-spacing: 0.8px; }

  .web-back {
    position: absolute; left: 0; right: 0; top: 295px;
    text-align: center; color: var(--white);
    font-size: 14px; letter-spacing: 3.2px;
  }
</style>
</head>
<body>
  <section class="card card-front">
    <div class="brand-front">
      <span class="brand-mark"></span>
      <div class="brand-name">Maplebrook</div>
      <div class="brand-sub">pediatric dentistry</div>
    </div>

    <ul class="doctors">
      <li>Mei-Ran Tsai, DMD</li>
      <li>Corinne Walbeck, DMD</li>
    </ul>

    <div class="contact">
      <div class="contact-line">
        <svg viewBox="0 0 16 16" aria-hidden="true"><path fill="#f0b323" d="M3.6 1.2l2.3 2.6-1.3 1.9c.9 2 2.5 3.6 4.5 4.6l1.9-1.3 2.6 2.3-1.6 2.6C6.4 13.6 2.3 9.5 1.1 3z"/></svg>
        <span>717.555.0193</span>
        <span class="gap"></span>
        <svg viewBox="0 0 16 16" aria-hidden="true"><circle cx="8" cy="8" r="7.5" fill="#f0b323"/><path fill="#fff" d="M5 4.5c1.5-.5 3 .3 3 1.6S6.3 7.4 6.7 9 5.3 11 4.4 10.4 3.8 6.5 5 4.5zm5.2 2.7c1 .2 1.8 1.2 1.5 2.5-.3 1.1-1.6 1.5-2 .6s.2-1.3 0-2.2.1-1 .5-.9z"/></svg>
        <span>maplebrookkidsdental.example</span>
      </div>
      <div>Maplebrook Pediatric Dentistry, 482 Quarry Lane</div>
      <div>Suite 517, Fernvale, PA 17588</div>
    </div>
  </section>

  <section class="card card-back">
    <div class="brand-back">
      <span class="brand-mark"></span>
      <div class="brand-name">Maplebrook</div>
      <div class="brand-sub">pediatric dentistry</div>
    </div>
    <div class="web-back">www.maplebrookkidsdental.example</div>
  </section>
</body>
</html>
```